Cedarvale Ridge College

We are looking to update our current webpage at www.cedarvaleridge.ca. We would like to make it modern, fresh and appealing to students. We want to keep our logo the same with the logo colours blended in as the primary colours and focus. We are open to reconfiguring content as well.
Reason: Hi, In the next 3 days we will have narrowed our search to 3 designs and will make a choice before the final deadline...
College

```html
<!DOCTYPE html>
<html lang="en">
<head>
<meta charset="utf-8">
<title>Cedarvale Ridge College</title>
<link rel="stylesheet" href="https://fonts.googleapis.com/css2?family=Open+Sans:wght@300;400;600;700&family=Oswald:wght@400&family=Roboto:wght@400;500&family=Bitter:wght@700&display=swap">
<style>
:root{
  --forest:#004035;
  --forest-deep:#013a30;
  --teal:#30705f;
  --navy:#0f2557;
  --paper:#efefef;
  --ink:#333333;
  --white:#ffffff;
  --foot-top:#3b3b3b;
  --foot-bottom:#121212;
}
*{margin:0;padding:0;box-sizing:border-box}
html,body{width:998px;height:1200px;overflow:hidden;background:var(--white)}
body{position:relative;font-family:"Open Sans",Arial,sans-serif;color:var(--ink)}
.abs{position:absolute}

/* header */
.site-header{left:0;top:0;width:998px;height:78px;background:var(--paper);border-top:3px solid var(--forest)}
.brand{left:110px;top:14px;display:flex;align-items:center;gap:10px}
.brand-dot{width:34px;height:34px;border-radius:50%;background:var(--forest)}
.brand-name{font-family:"Open Sans",Arial,sans-serif;font-weight:700;font-size:17px;line-height:19px;color:var(--forest);width:130px}
.phone-tab{left:693px;top:0;width:196px;height:32px}
.phone-tab span{position:absolute;left:65px;top:6px;font-family:"Open Sans",Arial,sans-serif;font-weight:600;font-size:15px;color:var(--white)}
.socials{left:736px;top:40px;display:flex;gap:10px}
.socials i{display:block;width:20px;height:20px;border-radius:3px;background:var(--navy)}

/* nav */
.main-nav{left:0;top:78px;width:998px;height:39px;background:var(--forest)}
.main-nav ul{list-style:none;display:flex;position:absolute;left:109px;top:0;height:39px}
.main-nav li{font-size:11px;font-weight:700;color:var(--white);line-height:39px;padding:0 6px;letter-spacing:.1px}
.main-nav li.current{background:var(--paper);color:var(--forest)}

/* hero */
.hero{left:0;top:117px;width:998px;height:333px;background:linear-gradient(100deg,#5a4a3e 0%,#6f8a4a 30%,#87a452 55%,#7f9a4a 75%,#5d7a38 100%)}
.hero-caption{left:525px;top:262px;width:363px;height:152px;background:rgba(40,45,35,.55);padding:8px 20px 0 20px;text-align:right;font-family:"Bitter",Georgia,serif;font-weight:700;font-size:23px;line-height:26.5px;color:var(--white)}
.hero-dots{left:837px;top:423px;display:flex;gap:6px}
.hero-dots i{display:block;width:13px;height:13px;background:#6b7a5a;border:1px solid #4c5740}
.hero-dots i.on{background:#000}

/* campus */
.section-title{left:0;top:466px;width:998px;text-align:center;font-weight:400;font-size:28px;color:var(--ink)}
.campus-card{top:520px;width:242px;height:78px;background:var(--navy);border-radius:2px}
.campus-card .icon{position:absolute;left:16px;top:12px;width:55px;height:55px;border-radius:50%;background:var(--white)}
.campus-card .icon i{position:absolute;left:14px;top:14px;width:27px;height:27px;border-radius:5px}
.campus-card span{position:absolute;left:86px;top:24px;font-family:"Oswald",Arial,sans-serif;font-size:21px;color:var(--white)}

/* welcome */
.welcome{left:0;top:626px;width:998px;height:238px;background:var(--teal)}
.welcome-kicker{left:111px;top:640px;font-family:"Oswald",Arial,sans-serif;font-size:22px;color:var(--white)}
.welcome-title{left:111px;top:660px;font-family:"Oswald",Arial,sans-serif;font-size:35px;color:var(--white)}
.welcome-rule{left:109px;top:714px;width:492px;border-top:2px dotted rgba(255,255,255,.55)}
.welcome-text{left:109px;top:726px;width:486px;font-family:"Roboto",Arial,sans-serif;font-size:12.6px;line-height:22.2px;color:var(--white)}
.read-more{left:525px;top:815px;font-family:"Roboto",Arial,sans-serif;font-size:12.6px;color:var(--white);text-decoration:underline}
.video-card{left:631px;top:638px;width:255px;height:203px;background:var(--white);border-radius:3px;box-shadow:0 0 14px rgba(0,0,0,.25)}
.video-frame{left:10px;top:12px;width:235px;height:156px;background:linear-gradient(90deg,#c9d1d8 0%,#e4e8ec 50%,#b7c3cf 100%)}
.video-bar{left:10px;top:168px;width:235px;height:24px;background:#2a2a2a;font-family:"Roboto",Arial,sans-serif;font-size:10px;color:var(--white)}

/* news */
.block-title{font-family:"Oswald",Arial,sans-serif;font-size:23px;color:var(--navy)}
.dash{border-top:1px dashed #9a9a9a}
.news-item{width:210px;height:50px}
.date{position:absolute;left:0;top:0;width:41px;height:46px;box-shadow:0 1px 2px rgba(0,0,0,.3)}
.date b{display:block;height:23px;background:var(--navy);color:var(--white);font-family:"Roboto",Arial,sans-serif;font-weight:500;font-size:15px;text-align:center;line-height:23px}
.date em{display:block;height:23px;background:#e8e8e8;border-bottom:2px solid #b5b5b5;color:var(--ink);font-style:normal;font-size:10.5px;text-align:center;line-height:22px}
.news-item h4{position:absolute;left:53px;top:-2px;font-size:11.5px;font-weight:700;color:#222;white-space:nowrap}
.news-item p{position:absolute;left:53px;top:15px;width:165px;font-size:10.8px;line-height:16px;color:#333}
.divider{left:614px;top:925px;width:1px;height:140px;background:#e0e0e0}
.admissions{left:636px;top:932px;width:243px;height:149px;background:var(--navy);border-radius:2px;padding:6px 0 0 8px}
.admissions ul{list-style:none}
.admissions li{font-family:"Roboto",Arial,sans-serif;font-size:12.3px;line-height:18.7px;color:var(--white);padding-left:14px;position:relative}
.admissions li:before{content:"";position:absolute;left:1px;top:6px;width:5px;height:5px;border-right:1.5px solid var(--white);border-bottom:1.5px solid var(--white);transform:rotate(-45deg)}

/* footer */
.site-footer{left:0;top:1097px;width:998px;height:103px;background:linear-gradient(var(--foot-top),var(--foot-bottom))}
.foot-links{left:0;top:1133px;width:998px;text-align:center;font-size:10.8px;color:var(--white)}
.foot-links span{padding:0 5px}
.foot-copy{left:0;top:1160px;width:998px;text-align:center;font-size:9.8px;color:var(--white)}
</style>
</head>
<body>

<header class="site-header abs">
  <div class="brand abs" style="top:11px">
    <div class="brand-dot"></div>
    <div class="brand-name">Cedarvale Ridge College</div>
  </div>
</header>

<svg class="phone-tab abs" viewBox="0 0 196 32" aria-hidden="true">
  <path d="M0 0H196L184 24Q180 32 172 32H24Q16 32 12 24Z" fill="#013a30"/>
  <circle cx="49" cy="16" r="9" fill="#fff"/>
  <path d="M45 11.5l2-1 2 3.2-1.4 1.2q1 2.2 3 3.2l1.2-1.4 3.2 2-1 2q-6-.5-9-9.2z" fill="#013a30"/>
</svg>
<div class="phone-tab abs" style="pointer-events:none"><span>604 555 0182</span></div>

<div class="socials abs"><i></i><i></i><i></i><i></i></div>

<nav class="main-nav abs">
  <ul>
    <li class="current">HOME</li>
    <li>ABOUT US</li>
    <li>CONTACT US</li>
    <li>CONSIDER CEDARVALE</li>
    <li>CURRENT STUDENTS</li>
    <li>ALUMNI</li>
    <li>SUPORTERS</li>
    <li>NEWS AND EVENTS</li>
    <li>CEDARVALE PARK</li>
  </ul>
</nav>

<section class="hero abs" role="img" aria-label="Photo of students walking across a green campus lawn beside brick buildings and trees"></section>
<div class="hero-caption abs">Educating, equipping and enriching Christians for Spirit-empowered ministry in the chruch and in the world</div>
<div class="hero-dots abs"><i class="on"></i><i></i><i></i></div>

<h2 class="section-title abs">OUR CAMPUS</h2>
<div class="campus-card abs" style="left:109px"><div class="icon"><i role="img" aria-label="Map icon" style="background:#9cc58a"></i></div><span>Map &amp; Directions</span></div>
<div class="campus-card abs" style="left:378px"><div class="icon"><i role="img" aria-label="Folded campus map icon" style="background:#d9c48c"></i></div><span>Campus Map</span></div>
<div class="campus-card abs" style="left:647px"><div class="icon"><i role="img" aria-label="Photo gallery icon" style="background:#8fb6d8"></i></div><span>Photo Gallery</span></div>

<section class="welcome abs"></section>
<div class="welcome-kicker abs">Welcome to</div>
<h1 class="welcome-title abs" style="font-weight:400">Cedarvale Ridge College</h1>
<div class="welcome-rule abs"></div>
<p class="welcome-text abs">Lorem ipsum dolor sit amet, consectetuer adipisemy nibh euismod tincidunt utre magmi aliquam erat volutpat. Ut wisi enim ad minim veniam quis nostrutation ullaeipit lobortisi nisl ut aliquip ex ea commodo consequis autem vel eum idolor in hendrer vulate velitm eonsequatvel illum dolore eu feugiat nulla facilisis at vero eros et accusao odiol digisml qui blandit praesent luptatum zzril delenit augue</p>
<div class="read-more abs">READ MORE</div>

<div class="video-card abs">
  <div class="video-frame abs" role="img" aria-label="Video still of a smiling staff member in an office with colleagues behind"></div>
  <svg class="abs" style="left:108px;top:68px" width="40" height="40" viewBox="0 0 40 40" aria-hidden="true">
    <circle cx="20" cy="20" r="20" fill="#fff"/><path d="M15 11L29 20L15 29Z" fill="#111"/>
  </svg>
  <div class="video-bar abs">
    <svg class="abs" style="left:0;top:0" width="235" height="24" viewBox="0 0 235 24" aria-hidden="true">
      <rect width="22" height="24" fill="#3d3d3d"/>
      <path d="M8 7L15 12L8 17Z" fill="#fff"/>
      <rect x="71" y="9" width="101" height="6" rx="3" fill="#666"/>
      <circle cx="116" cy="12" r="5" fill="#aaa"/>
      <path d="M215 9h3l4-3v12l-4-3h-3z" fill="#fff"/>
      <path d="M224 8q3 4 0 8" stroke="#fff" fill="none" stroke-width="1.2"/>
    </svg>
    <span class="abs" style="left:35px;top:6px">04:59</span>
    <span class="abs" style="left:180px;top:6px">10:35</span>
  </div>
</div>

<h3 class="block-title abs" style="left:107px;top:880px;font-weight:400">News &amp; Events</h3>
<svg class="abs" style="left:536px;top:889px" width="34" height="16" viewBox="0 0 34 16" aria-hidden="true">
  <path d="M10 2L4 8L10 14M22 2L28 8L22 14" stroke="#0f2557" stroke-width="2.2" fill="none"/>
</svg>
<div class="dash abs" style="left:107px;top:921px;width:460px"></div>

<div class="news-item abs" style="left:109px;top:931px"><div class="date"><b>18</b><em>NOV</em></div><h4>Lorem ipsum dolor sit..</h4><p>Sed diam nonmy nibh eumod tincidun ut laoreet dolore magna</p></div>
<div class="news-item abs" style="left:356px;top:931px"><div class="date"><b>20</b><em>NOV</em></div><h4>Lorem ipsum dolor sit..</h4><p>Sed diam nonmy nibh eumod tincidun ut laoreet dolore magna</p></div>
<div class="news-item abs" style="left:109px;top:1002px"><div class="date"><b>19</b><em>NOV</em></div><h4>Lorem ipsum dolor sit..</h4><p>Sed diam nonmy nibh eumod tincidun ut laoreet dolore magna</p></div>
<div class="news-item abs" style="left:356px;top:1002px"><div class="date"><b>21</b><em>NOV</em></div><h4>Lorem ipsum dolor sit..</h4><p>Sed diam nonmy nibh eumod tincidun ut laoreet dolore magna</p></div>

<div class="divider abs"></div>

<h3 class="block-title abs" style="left:636px;top:880px;font-weight:400">Admissions</h3>
<div class="dash abs" style="left:636px;top:921px;width:253px"></div>
<div class="admissions abs">
  <ul>
    <li>Download the full Catalogue</li>
    <li>Apply Today (Application Package)</li>
    <li>Information Request</li>
    <li>Browse our Programs</li>
    <li>Download Forms</li>
    <li>Admissions Information</li>
    <li>Campus Directory</li>
  </ul>
</div>

<footer class="site-footer abs"></footer>
<div class="foot-links abs">
  <span>Home</span>|<span>About Us</span>|<span>Contact Us</span>|<span>Consider Cedarvale</span>|<span>Current Students</span>|<span>Alumni</span>|<span>Suporters</span>|<span>News And Events</span>|<span>Cedarvale Park</span>
</div>
<div class="foot-copy abs">© 2014 | E-file Copyright | All Rights Reserved. | Privacy Policy</div>

</body>
</html>
```